Trucking Company Website Design

We are working with a Trucking company in California. They provide trucking services for dirt, gravel, landscape bark, and landscape materials.

As you might imagine, there are no websites we could find for inspiration for trucking companies.

Thank you for taking the time to consider designing a website for us. We are web developers based in Stockton, CA, USA. Most of our projects go through the same process. Understanding this process may help you win a project with us. We custom-code all of our websites in-house. We don’t have any requirements as to what tools you use for your design, but we ask that you follow these guidelines.

IMAGES:
If you use any images or icons in the design, we ask that you have a link to the asset so we can purchase the image/icon. Most of the designs we submit do not have the customer’s images on them unless they have some great images. Be creative; show us the feeling you are trying to portray with your image choices. Use any royalty-free site you choose. We subscribe to Quillo and mainly use their images, but we can purchase images outside of Quillo. PLEASE NOTE: we will not submit designs to clients with watermarks on the images.

FONTS:
We ask that you identify the fonts you’re using in the design. This can be done in a message if you want. We typically use Varnex Fonts and Quillo Fonts.

CONTENT:
We're always open to different content and ideas. We often submit designs with stock images so the client can see our vision. We typically take pictures after the website launch to use their images with our vision. Lorem Ipsum is fine for paragraphs, but we ask that you make the Headers with correct English. We want to be able to show the vision and identify the sections of the website.

INSPIRATION:
We typically add a couple of links in the brief of websites we like to help you get started in your design.

REVISIONS:
We do not often ask for revisions of the designs unless we see something in the design that may not appeal to the client. If there are slight changes that we want to make, we do that in the development process.

FEEDBACK:
We rarely give feedback on designs during the design process. We are working on many website projects and do not have the time to provide feedback. We usually respond if your request is well thought out and asks specific questions, but a note asking “feedback, please” usually goes unanswered.

```html
<!DOCTYPE html>
<html lang="en">
<head>
<meta charset="utf-8">
<title>Ridgeline Haul – Trucking Services</title>
<link href="https://fonts.googleapis.com/css2?family=Montserrat:wght@500;600;700;800&family=Open+Sans:wght@400;600&display=swap" rel="stylesheet">
<style>
:root{
  --red:#e42528;
  --navy:#1b4e86;
  --blue:#2a7dbf;
  --ink:#2a2a2a;
  --muted:#6b6b6b;
  --paper:#ffffff;
  --mist:#f1f1f1;
  --charcoal:#3a3a3a;
  --night:#2b2b2b;
}
*{box-sizing:border-box;margin:0;padding:0}
html,body{width:1200px;height:3964px;overflow:hidden}
body{font-family:"Open Sans",sans-serif;color:var(--ink);background:var(--paper);position:relative}
h1,h2,h3,.brand,.nav,.btn{font-family:"Montserrat",sans-serif}
.btn{display:inline-block;background:var(--red);color:#fff;font-size:13px;font-weight:700;padding:11px 22px;letter-spacing:.5px;text-decoration:none}
.btn-sm{font-size:11px;padding:8px 16px}

/* header */
.site-header{height:112px;position:relative;background:#fff}
.brand{position:absolute;left:28px;top:22px;display:flex;align-items:center;gap:10px;color:var(--navy);font-weight:800;font-size:26px;line-height:1}
.brand small{display:block;font-size:17px;font-weight:800;letter-spacing:2px}
.brand .mark{width:34px;height:34px;background:var(--red)}
.contact{position:absolute;top:18px;display:flex;gap:10px;font-size:13px;color:var(--muted)}
.contact b{display:block;font-family:"Montserrat",sans-serif;font-size:12px;color:var(--navy);letter-spacing:1px}
.contact .ico{width:30px;height:30px;border-radius:50%;background:var(--navy);display:flex;align-items:center;justify-content:center}
.contact-mail{left:540px}.contact-call{left:940px}
.contact-call span{font-size:16px;font-weight:600;color:var(--ink)}
.nav{position:absolute;left:540px;top:70px;display:flex;gap:44px;font-size:15px;font-weight:600;color:var(--ink)}
.nav .active{color:var(--red)}

/* hero */
.hero{height:548px;position:relative;background:linear-gradient(180deg,#c7cfd4 0%,#a5a79b 45%,#7b6a55 100%)}
.hero-text{position:absolute;left:130px;top:92px;width:400px;color:#fff}
.hero-text h1{font-size:52px;line-height:1.08;font-weight:800;margin-bottom:16px}
.hero-text p{font-size:18px;line-height:1.4;margin-bottom:32px}
.dots{position:absolute;left:560px;bottom:36px;display:flex;gap:10px}
.dots i{width:10px;height:10px;border-radius:50%;background:#fff;opacity:.6}
.dots i:first-child{opacity:1}

/* welcome */
.welcome{height:540px;position:relative}
.welcome-text{position:absolute;left:130px;top:62px;width:390px}
.welcome-text h2{font-size:30px;font-weight:800;line-height:1.2;color:var(--ink)}
.welcome-text h2 span{color:var(--navy)}
.accent{display:inline-block;width:60px;height:4px;background:var(--red);margin:14px 0 20px}
.welcome-text p{font-size:14px;line-height:1.75;color:var(--muted);margin-bottom:30px}
.welcome-photo{position:absolute;left:560px;top:20px}

/* services */
.services{height:1560px;background:var(--mist);position:relative}
.services h2{position:absolute;top:22px;width:100%;text-align:center;font-size:28px;font-weight:800}
.services h2::after{content:"";display:block;width:60px;height:4px;background:var(--red);margin:12px auto 0}
.service{position:absolute;left:132px;width:936px;height:338px;background:#fff}
.service .photo{position:absolute;top:0;width:428px;height:338px}
.service .copy{position:absolute;top:34px;width:440px}
.service h3{font-size:34px;font-weight:800;margin-bottom:8px}
.service ul{list-style:none;margin-bottom:24px}
.service li{font-size:14px;color:var(--muted);line-height:1.75;padding-left:18px;position:relative}
.service li::before{content:"";position:absolute;left:0;top:9px;width:7px;height:7px;border-radius:50%;background:var(--red)}
.service.left .photo{left:0}.service.left .copy{left:448px}
.service.right .photo{right:0}.service.right .copy{left:16px}

/* why */
.why{height:370px;position:relative;background:linear-gradient(180deg,#9aa3a6 0%,#6d7375 60%,#4b4d4c 100%)}
.why h2{position:absolute;top:120px;width:100%;text-align:center;color:#fff;font-size:28px;font-weight:800}
.why-band{position:absolute;left:0;right:0;bottom:0;height:122px;background:var(--blue);display:flex;justify-content:center;gap:20px;align-items:center}
.feature{display:flex;align-items:center;gap:14px;width:240px;color:#fff;font-size:14px;line-height:1.5}
.feature .ico{flex:0 0 48px;height:48px;border:2px solid #fff;border-radius:50%;display:flex;align-items:center;justify-content:center}

/* testimonials */
.testimonials{height:610px;background:var(--mist);position:relative}
.testimonials h2{position:absolute;top:14px;width:100%;text-align:center;font-size:28px;font-weight:800}
.testimonials h2::after{content:"";display:block;width:60px;height:4px;background:var(--red);margin:12px auto 0}
.cards{position:absolute;top:112px;left:0;right:0;display:flex;justify-content:center;gap:18px}
.card{width:198px;height:468px;background:#fff;padding:30px 22px;text-align:center}
.card .q{font-family:"Montserrat",sans-serif;font-size:46px;font-weight:800;color:var(--blue);line-height:.8;display:block;margin-bottom:14px}
.card p{font-size:13.5px;line-height:1.75;color:var(--muted);margin-bottom:18px}
.card hr{border:0;height:2px;width:40px;background:var(--red);margin:0 auto 12px}
.card b{font-family:"Montserrat",sans-serif;font-size:15px}
.tdots{position:absolute;bottom:18px;left:570px;display:flex;gap:10px}
.tdots i{width:9px;height:9px;border-radius:50%;background:#bbb}.tdots i:first-child{background:var(--red)}

/* footer */
.site-footer{height:264px;position:relative;background:#fff}
.footer-art{position:absolute;left:60px;top:14px;width:300px;height:120px;border-radius:6px;background:linear-gradient(180deg,#f2c230 0%,#e6a91d 60%,#555 100%)}
.site-footer .brand{left:auto;right:140px;top:60px}
.footer-nav{position:absolute;left:0;right:0;top:158px;height:40px;background:var(--charcoal);display:flex;justify-content:center;align-items:center;gap:48px;color:#fff;font-family:"Montserrat",sans-serif;font-size:14px;font-weight:600}
.footer-bottom{position:absolute;left:0;right:0;top:198px;height:66px;background:var(--night);color:#bbb;font-size:12px;display:flex;align-items:center;justify-content:space-between;padding:0 40px}
.social{display:flex;align-items:center;gap:8px}
.social i{width:22px;height:22px;border-radius:50%;background:#fff;opacity:.85}
</style>
</head>
<body>

<header class="site-header">
  <div class="brand"><div>RIDGELINE<small>HAUL</small></div><span class="mark"></span></div>
  <div class="contact contact-mail">
    <span class="ico"><svg width="16" height="12" viewBox="0 0 16 12"><rect x="1" y="1" width="14" height="10" fill="none" stroke="#fff" stroke-width="1.5"/><path d="M1 1l7 6 7-6" fill="none" stroke="#fff" stroke-width="1.5"/></svg></span>
    <div><b>EMAIL US</b>info@ridgelinehaul.com</div>
  </div>
  <div class="contact contact-call">
    <span class="ico"><svg width="14" height="14" viewBox="0 0 24 24"><path fill="#fff" d="M6.6 10.8a15 15 0 006.6 6.6l2.2-2.2a1 1 0 011-.25 11 11 0 003.6.6 1 1 0 011 1V20a1 1 0 01-1 1A17 17 0 013 4a1 1 0 011-1h3.5a1 1 0 011 1 11 11 0 00.6 3.6 1 1 0 01-.25 1z"/></svg></span>
    <div><b>CALL US</b><span>+1 888 888 8888</span></div>
  </div>
  <nav class="nav"><span class="active">HOME</span><span>ABOUT US</span><span>SERVICES</span><span>LOCATIONS</span><span>CONTACT US</span></nav>
</header>

<section class="hero" role="img" aria-label="Photo of a dump truck driving on a gravel road">
  <div class="hero-text">
    <h1>TRUCKING SERVICES FOR GRAVEL</h1>
    <p>Lorem ipsum dolor sit amet, cons ectetur adipiscing elit, sed do eiusmod tempor incididunt</p>
    <span class="btn">READ MORE</span>
  </div>
  <div class="dots"><i></i><i></i><i></i></div>
</section>

<section class="welcome">
  <div class="welcome-text">
    <h2>WELCOME TO<br><span>RIDGELINE HAUL</span></h2>
    <span class="accent"></span>
    <p>Sed ut perspiciatis unde omnis iste natus error sit voluptatem accusantium doloremque laudantium, totam rem aperiam, eaque ipsa quae ab illo inventore veritatis et quasi architecto beatae vitae dicta sunt explicabo. Nemo enim ipsam voluptatem quia voluptas sit aspernatur aut odit aut fugit, sed quia consequuntur magni dolores eos qui ratione voluptatem sequi nesciunt. Neque porro quisquam est, qui dolorem ipsum quia dolor sit amet, consectetur, adipisci velit, sed quia non numquam eius modi tempora incidunt ut labore et dolore magnam aliquam quaerat voluptatem.</p>
    <span class="btn">READ MORE</span>
  </div>
  <svg class="welcome-photo" width="520" height="500" viewBox="0 0 520 500" role="img" aria-label="Photo of a yellow dump truck on a dirt site">
    <defs><linearGradient id="wg" x1="0" y1="0" x2="0" y2="1"><stop offset="0" stop-color="#b9cbe0"/><stop offset=".55" stop-color="#c9b27f"/><stop offset="1" stop-color="#8e7451"/></linearGradient></defs>
    <polygon points="40,0 380,0 520,250 380,500 40,500 150,250" fill="url(#wg)"/>
  </svg>
</section>

<section class="services">
  <h2>TRUCKING SERVICES</h2>

  <article class="service left" style="top:92px">
    <div class="photo" role="img" aria-label="Photo of a truck unloading dirt" style="background:linear-gradient(180deg,#6b7d8f,#8a7a62)"></div>
    <div class="copy">
      <h3>DIRT</h3>
      <ul><li>Lorem ipsum dolor sit amet consectet</li><li>But I must explain to you how all this</li><li>Sed ut perspiciatis unde omnis iste natus</li><li>Ut enim ad minima veniam, quis nostrum</li><li>Nor again is there anyone who loves or pursues</li><li>At vero eos et accusamus et iusto odio dignissimos</li></ul>
      <span class="btn btn-sm">READ MORE</span>
    </div>
  </article>

  <article class="service right" style="top:452px">
    <div class="copy">
      <h3>GRAVEL</h3>
      <ul><li>Lorem ipsum dolor sit amet consectet</li><li>But I must explain to you how all this</li><li>Sed ut perspiciatis unde omnis iste natus</li><li>Ut enim ad minima veniam, quis nostrum</li><li>Nor again is there anyone who loves or pursues</li><li>At vero eos et accusamus et iusto odio dignissimos</li></ul>
      <span class="btn btn-sm">READ MORE</span>
    </div>
    <div class="photo" role="img" aria-label="Photo of a red dump truck tipping gravel" style="background:linear-gradient(180deg,#aebfcc,#a0523f 55%,#9b9389)"></div>
  </article>

  <article class="service left" style="top:808px">
    <div class="photo" role="img" aria-label="Photo of a pile of landscape bark mulch" style="background:linear-gradient(160deg,#8a5a3a,#6e4228)"></div>
    <div class="copy">
      <h3>LANDSCAPE BARK</h3>
      <ul><li>Lorem ipsum dolor sit amet consectet</li><li>But I must explain to you how all this</li><li>Sed ut perspiciatis unde omnis iste natus</li><li>Ut enim ad minima veniam, quis nostrum</li><li>Nor again is there anyone who loves or pursues</li><li>At vero eos et accusamus et iusto odio dignissimos</li></ul>
      <span class="btn btn-sm">READ MORE</span>
    </div>
  </article>

  <article class="service right" style="top:1160px">
    <div class="copy">
      <h3>LANDSCAPE MATERIALS</h3>
      <ul><li>Lorem ipsum dolor sit amet consectet</li><li>But I must explain to you how all this</li><li>Sed ut perspiciatis unde omnis iste natus</li><li>Ut enim ad minima veniam, quis nostrum</li><li>Nor again is there anyone who loves or pursues</li><li>At vero eos et accusamus et iusto odio dignissimos</li></ul>
      <span class="btn btn-sm">READ MORE</span>
    </div>
    <div class="photo" role="img" aria-label="Photo of a landscaped garden with lawn and shrubs" style="background:linear-gradient(180deg,#3f7a34,#7fbf3f)"></div>
  </article>
</section>

<section class="why" role="img" aria-label="Photo of a truck driver standing in front of a fleet of trucks">
  <h2>WHY CHOOSE US</h2>
  <div class="why-band">
    <div class="feature"><span class="ico"><svg width="22" height="22" viewBox="0 0 24 24"><path d="M4 12l5 5L20 6" fill="none" stroke="#fff" stroke-width="2.5"/></svg></span>Happy, friendly and knowledgeable staff to take care of you</div>
    <div class="feature"><span class="ico"><svg width="22" height="22" viewBox="0 0 24 24"><circle cx="12" cy="12" r="9" fill="none" stroke="#fff" stroke-width="2"/><path d="M12 7v5l3 3" fill="none" stroke="#fff" stroke-width="2"/></svg></span>On-time delivery and same-day delivery available</div>
    <div class="feature"><span class="ico"><svg width="22" height="22" viewBox="0 0 24 24"><path d="M3 8h11v8H3zM14 11h4l3 3v2h-7z" fill="none" stroke="#fff" stroke-width="2"/></svg></span>The freshest and longest-lasting mulch in town</div>
    <div class="feature"><span class="ico"><svg width="22" height="22" viewBox="0 0 24 24"><path d="M3 18l9-12 9 12z" fill="none" stroke="#fff" stroke-width="2"/></svg></span>Bulk landscape materials in smaller quantities</div>
  </div>
</section>

<section class="testimonials">
  <h2>TESTIMONIALS</h2>
  <div class="cards">
    <div class="card"><span class="q">“</span><p>Sed ut perspiciatis unde omnis iste natus error sit voluptatem accusantium doloremque laudantium, totam rem aperiam, eaque ipsa quae ab illo inventore veritatis et quasi architecto beatae vitae dicta sunt explicabo.</p><hr><b>Dorian</b></div>
    <div class="card"><span class="q">“</span><p>Sed ut perspiciatis unde omnis iste natus error sit voluptatem accusantium doloremque laudantium, totam rem aperiam, eaque ipsa quae ab illo inventore veritatis et quasi architecto beatae vitae dicta sunt explicabo.</p><hr><b>Dorian</b></div>
    <div class="card"><span class="q">“</span><p>Sed ut perspiciatis unde omnis iste natus error sit voluptatem accusantium doloremque laudantium, totam rem aperiam, eaque ipsa quae ab illo inventore veritatis et quasi architecto beatae vitae dicta sunt explicabo.</p><hr><b>Dorian</b></div>
    <div class="card"><span class="q">“</span><p>Sed ut perspiciatis unde omnis iste natus error sit voluptatem accusantium doloremque laudantium, totam rem aperiam, eaque ipsa quae ab illo inventore veritatis et quasi architecto beatae vitae dicta sunt explicabo.</p><hr><b>Dorian</b></div>
    <div class="card"><span class="q">“</span><p>Sed ut perspiciatis unde omnis iste natus error sit voluptatem accusantium doloremque laudantium, totam rem aperiam, eaque ipsa quae ab illo inventore veritatis et quasi architecto beatae vitae dicta sunt explicabo.</p><hr><b>Dorian</b></div>
  </div>
  <div class="tdots"><i></i><i></i><i></i></div>
</section>

<footer class="site-footer">
  <div class="footer-art" role="img" aria-label="Illustration of a yellow truck carrying a load of gravel"></div>
  <div class="brand"><div>RIDGELINE<small>HAUL</small></div><span class="mark"></span></div>
  <nav class="footer-nav"><span>HOME</span><span>ABOUT US</span><span>SERVICES</span><span>LOCATIONS</span><span>CONTACT US</span></nav>
  <div class="footer-bottom">
    <div class="social">Follow us <i></i><i></i><i></i><i></i></div>
    <div>Copyright © 2021 All Rights Reserved</div>
  </div>
</footer>

</body>
</html>
```